Locksmith Business Cards

My father-in-law is in need of new business cards for his locksmith business and I need to impress him. Kindly help me out!

You can see the previous business card attached. It is a family run business in North Wales.

No individual names on the cards.

Key Things to Feature:
- The words "Prompt", "Local", "Reliable" (as you can see under the logo on the website)
- 24h Emergency Service
- Covering All of North Wales, the Wirral and Chester
- The color blue
- A key or a lock would be interesting (similar to the ones that come up when you google locksmith business card)

Optional (only if design includes bullet points, like the example below):
https://imgvaultcdn.net/samples/208314/55172/55172_3904821_208314_image.jpg
- Residential / Commercial / Automotive
- Alarms & Cameras
- Key Cutting & Safes

https://www.brynhafod-locksmiths.co.uk/

Industry/Entity Type

Locksmith

Contact Information for Business Card

01632 960 418
07700 900 362
brynhafodlocksmiths@mailvane.com
Brynhafod Locksmiths, The Willow Barn, 7 Tannery Rd., Llandudno LL99 4QX
www.brynhafod-locksmiths.co.uk

Requirements
Must have
• - The words "Prompt", "Local", "Reliable" (as you can see under the logo on the website)
• - 24h Emergency Service
• - Covering All of North Wales, the Wirral and Chester
Nice to have
• - A key or a lock would be interesting (similar to the ones that come up when you google locksmith business card)

```html
<!DOCTYPE html>
<html lang="en">
<head>
<meta charset="utf-8">
<title>Brynhafod Locksmiths – Business Cards</title>
<link rel="stylesheet" href="https://fonts.googleapis.com/css2?family=Oswald:wght@500&family=Open+Sans:wght@400;600;700;800&display=swap">
<style>
  :root {
    --navy: #25296a;
    --periwinkle: #4a5ea3;
    --soft-blue: #5a6fb8;
    --white: #ffffff;
    --grey: #9aa3ad;
    --backdrop: #1f1f21;
  }
  * { box-sizing: border-box; margin: 0; padding: 0; }
  html, body { width: 1200px; height: 1021px; overflow: hidden; }
  body {
    background: var(--backdrop);
    font-family: "Open Sans", sans-serif;
    position: relative;
  }
  .card {
    position: absolute;
    left: 250px;
    width: 700px;
    height: 400px;
    overflow: hidden;
    box-shadow: 0 10px 30px rgba(0,0,0,.45);
  }
  .card--back { top: 60px; background: var(--navy); color: var(--white); }
  .card--front { top: 540px; background: var(--white); color: var(--navy); }

  .brand {
    display: flex; align-items: center; gap: 14px;
    font-family: "Oswald", sans-serif; font-weight: 500;
    text-transform: uppercase; line-height: .95;
  }
  .brand__mark { width: 44px; height: 44px; flex: none; }
  .brand__name { font-size: 44px; letter-spacing: .5px; }

  /* back */
  .card--back .brand { position: absolute; left: 200px; top: 58px; }
  .card--back .brand__mark { background: var(--white); }
  .card--back .brand__name { color: var(--white); }
  .established {
    position: absolute; left: 130px; right: 130px; top: 160px;
    display: flex; align-items: center; gap: 14px;
    color: var(--soft-blue); font-size: 17px; letter-spacing: 1px;
  }
  .established::before, .established::after {
    content: ""; flex: 1; height: 1px; background: var(--soft-blue);
  }
  .services {
    position: absolute; left: 0; right: 0; top: 198px;
    list-style: none; text-align: center;
    font-size: 18px; line-height: 1.35; letter-spacing: .5px;
  }
  .back-band { position: absolute; left: 0; right: 0; background: var(--periwinkle); }
  .back-band--upper { top: 300px; height: 26px; }
  .back-band--lower { bottom: 0; height: 22px; }
  .website {
    position: absolute; left: 0; right: 0; top: 334px; text-align: center;
    font-weight: 700; font-size: 20px; letter-spacing: 1.5px;
  }

  /* front */
  .card--front .brand { position: absolute; left: 40px; top: 34px; }
  .card--front .brand__mark { background: var(--navy); }
  .card--front .brand__name { color: var(--navy); }
  .contact { position: absolute; left: 60px; top: 140px; list-style: none; }
  .contact li { display: flex; align-items: center; gap: 8px; }
  .contact__phone { font-weight: 800; font-size: 24px; letter-spacing: .5px; line-height: 1.2; }
  .contact__email { font-size: 16px; margin-top: 2px; }
  .contact__icon { width: 16px; height: 16px; fill: none; stroke: var(--periwinkle); stroke-width: 2; }
  .address { position: absolute; left: 80px; top: 232px; font-size: 16px; line-height: 1.3; text-align: center; }
  .tagline-badge {
    position: absolute; right: 50px; top: 60px;
    width: 250px; height: 250px; border-radius: 50%;
    background: var(--navy);
    display: flex; align-items: center; justify-content: center;
  }
  .tagline {
    background: var(--white); color: var(--navy);
    font-weight: 800; font-size: 24px; line-height: 1.15; text-align: center;
    padding: 14px 26px;
  }
  .emergency-band {
    position: absolute; left: 0; right: 0; top: 292px; height: 36px;
    background: var(--periwinkle); color: var(--white);
    font-weight: 800; font-size: 24px; letter-spacing: 1.5px;
    display: flex; align-items: center; padding-left: 150px;
  }
  .coverage {
    position: absolute; left: 0; right: 0; top: 338px; text-align: center;
    font-size: 19px; letter-spacing: .3px;
  }
  .front-band { position: absolute; left: 0; right: 0; bottom: 0; height: 18px; background: var(--periwinkle); }
</style>
</head>
<body>

<section class="card card--back" aria-label="Card back">
  <div class="brand">
    <span class="brand__mark"></span>
    <span class="brand__name">Brynhafod<br>Locksmiths</span>
  </div>
  <p class="established">Est Since 1989</p>
  <ul class="services">
    <li>Residential / Commercial / Automotive</li>
    <li>Alarms &amp; Cameras</li>
    <li>Key Cutting &amp; Safes</li>
  </ul>
  <div class="back-band back-band--upper"></div>
  <p class="website">www.brynhafod-locksmiths.co.uk</p>
  <div class="back-band back-band--lower"></div>
</section>

<section class="card card--front" aria-label="Card front">
  <div class="brand">
    <span class="brand__mark"></span>
    <span class="brand__name">Brynhafod<br>Locksmiths</span>
  </div>
  <ul class="contact">
    <li class="contact__phone">
      <svg class="contact__icon" viewBox="0 0 16 16"><path d="M3 1h3l1 4-2 1c1 2 3 4 5 5l1-2 4 1v3c0 1-1 2-2 2C7 15 1 9 1 3c0-1 1-2 2-2z" fill="#4a5ea3" stroke="none"/></svg>
      01632 960 418
    </li>
    <li class="contact__phone">
      <svg class="contact__icon" viewBox="0 0 16 16"><rect x="4" y="1" width="8" height="14" rx="1.5"/><line x1="7" y1="12.5" x2="9" y2="12.5"/></svg>
      07700 900 362
    </li>
    <li class="contact__email">
      <svg class="contact__icon" viewBox="0 0 16 16"><rect x="1" y="3" width="14" height="10"/><polyline points="1,3 8,9 15,3"/></svg>
      brynhafodlocksmiths@mailvane.com
    </li>
  </ul>
  <p class="address">The Willow Barn, 7 Tannery Rd.<br>Llandudno LL99 4QX</p>
  <div class="tagline-badge">
    <p class="tagline">Prompt.<br>Local.<br>Reliable</p>
  </div>
  <div class="emergency-band">24H EMERGENCY SERVICE</div>
  <p class="coverage">Covering All of North Wales, the Wirral and Chester</p>
  <div class="front-band"></div>
</section>

</body>
</html>
```